KOVAR Design

We have a 5 part framework that companies use to plot their social media strategies and digital transformation activity. We would like to display the 5 elements in a circular format (please see the attachment for our current design - we want to get a better version of that).

The five elements and their meaning can be read about here: http://plenmorastudio.com/kovar/what-is-kovar/
We would like to see designs that fit our corporate image but also maintain informality and simplicity…. Ive included another image of some of the icons we've been using and enjoying to give an understanding of the stuff we like

Target Market(s)

Corporates

Industry/Entity Type

Digital

Logo Text

Brokerage, Integration, Trust, Incentives, Leadership

Colors
0255a3

Requirements
Must have
• Must be circular in format with each element neatly labelled - PLEASE REVIEW OUR CURRENT VERSION IN THE ATTACHMENTS

```html
<!DOCTYPE html>
<html lang="en">
<head>
<meta charset="utf-8">
<title>Community Management Framework</title>
<link href="https://fonts.googleapis.com/css2?family=Arimo:wght@400;700&display=swap" rel="stylesheet">
<style>
  :root {
    --page-bg: #f7fbfd;
    --ring-blue: #0a7dc2;
    --node-navy: #0b3a6b;
    --ink-navy: #0b3a6b;
    --text-light: #ffffff;
    --icon-light: #e4e8ee;
    --icon-soft: #4f7fae;
  }
  html, body {
    margin: 0;
    padding: 0;
    width: 1200px;
    height: 900px;
    overflow: hidden;
    background: var(--page-bg);
  }
  .framework {
    display: block;
    width: 1200px;
    height: 900px;
    font-family: "Arimo", Arial, sans-serif;
  }
  .orbit { fill: none; stroke: var(--ring-blue); stroke-width: 16; }
  .node-rim { fill: var(--ring-blue); }
  .node-core { fill: var(--node-navy); }
  .badge { fill: var(--ring-blue); stroke: var(--node-navy); stroke-width: 2; }
  .badge-letter { fill: var(--text-light); font-size: 15px; font-weight: 700; text-anchor: middle; }
  .node-label { fill: var(--text-light); font-size: 21px; text-anchor: middle; }
  .hub-fill { fill: #ffffff; }
  .hub-rim { fill: none; stroke: var(--ring-blue); stroke-width: 8; }
  .hub-title { fill: var(--ink-navy); font-size: 20px; font-weight: 700; text-anchor: middle; }
  .figure-area { fill: var(--icon-soft); }
  .hub-figure-area { fill: var(--ring-blue); }
  .chart-bar { fill: var(--icon-light); }
  .chart-bar--accent { fill: var(--ring-blue); }
  .chart-arrow { fill: none; stroke: var(--text-light); stroke-width: 5; stroke-linejoin: round; }
  .chart-arrow-head { fill: var(--text-light); }
  .monitor-screen { fill: var(--node-navy); stroke: var(--ring-blue); stroke-width: 3; }
  .monitor-base { fill: var(--ring-blue); }
  .monitor-sign { fill: var(--icon-light); font-size: 17px; text-anchor: middle; }
</style>
</head>
<body>
<svg class="framework" viewBox="0 0 1200 900" xmlns="http://www.w3.org/2000/svg">
  <defs>
    <clipPath id="hub-clip"><circle cx="600" cy="470" r="99"/></clipPath>
  </defs>

  <circle class="orbit" cx="600" cy="472" r="248"/>

  <g class="hub">
    <circle class="hub-fill" cx="600" cy="470" r="103"/>
    <text class="hub-title" x="600" y="454">Community</text>
    <text class="hub-title" x="600" y="479">management</text>
    <g clip-path="url(#hub-clip)">
      <rect class="hub-figure-area" x="535" y="508" width="130" height="70" rx="22" role="img" aria-label="Group of three people"/>
    </g>
    <circle class="hub-rim" cx="600" cy="470" r="103"/>
  </g>

  <g class="node node--brokerage">
    <circle class="node-rim" cx="600" cy="228" r="96"/>
    <circle class="node-core" cx="600" cy="228" r="85"/>
    <circle class="badge" cx="600" cy="160" r="12"/>
    <text class="badge-letter" x="600" y="165.5">B</text>
    <text class="node-label" x="600" y="198">Brokerage</text>
    <rect class="figure-area" x="536" y="218" width="128" height="78" rx="20" role="img" aria-label="Central person connecting two others"/>
  </g>

  <g class="node node--integration">
    <circle class="node-rim" cx="838" cy="405" r="96"/>
    <circle class="node-core" cx="838" cy="405" r="85"/>
    <circle class="badge" cx="838" cy="333" r="12"/>
    <text class="badge-letter" x="838" y="338.5">I</text>
    <text class="node-label" x="838" y="373">Integration</text>
    <rect class="figure-area" x="786" y="388" width="104" height="88" rx="20" role="img" aria-label="Three people talking with speech bubbles"/>
  </g>

  <g class="node node--trust">
    <circle class="node-rim" cx="748" cy="680" r="96"/>
    <circle class="node-core" cx="748" cy="680" r="85"/>
    <circle class="badge" cx="748" cy="608" r="12"/>
    <text class="badge-letter" x="748" y="613.5">T</text>
    <text class="node-label" x="748" y="654">Trust building</text>
    <rect class="chart-bar" x="708" y="722" width="10" height="38"/>
    <rect class="chart-bar" x="726" y="708" width="10" height="52"/>
    <rect class="chart-bar" x="744" y="716" width="10" height="44"/>
    <rect class="chart-bar" x="762" y="700" width="10" height="60"/>
    <rect class="chart-bar--accent" x="780" y="690" width="10" height="70"/>
    <polyline class="chart-arrow" points="700,722 728,696 748,706 786,676"/>
    <polygon class="chart-arrow-head" points="796,666 780,670 790,682"/>
  </g>

  <g class="node node--incentives">
    <circle class="node-rim" cx="455" cy="676" r="96"/>
    <circle class="node-core" cx="455" cy="676" r="85"/>
    <circle class="badge" cx="455" cy="609" r="12"/>
    <text class="badge-letter" x="455" y="614.5">I</text>
    <text class="node-label" x="455" y="650">Incentives</text>
    <rect class="monitor-screen" x="428" y="662" width="54" height="30" rx="2"/>
    <rect class="monitor-base" x="424" y="693" width="62" height="5" rx="1"/>
    <text class="monitor-sign" x="455" y="684">$</text>
    <rect class="figure-area" x="406" y="704" width="98" height="52" rx="18" role="img" aria-label="Three people"/>
  </g>

  <g class="node node--leadership">
    <circle class="node-rim" cx="366" cy="393" r="96"/>
    <circle class="node-core" cx="366" cy="393" r="85"/>
    <circle class="badge" cx="366" cy="330" r="12"/>
    <text class="badge-letter" x="366" y="335.5">L</text>
    <text class="node-label" x="366" y="369">Leadership</text>
    <rect class="figure-area" x="330" y="378" width="72" height="92" rx="18" role="img" aria-label="Person standing with a folder on a spotlight"/>
  </g>
</svg>
</body>
</html>
```